Location-Based project

I need a webdesign for a project similar to bramblenet, tiparno or kelvik. The feel should be more like bramblenet.
An example of the content of the site can be found on http://www.varquist.nl/maddox/site
The idea of the project is searching and performing actions based on the real location of your mobile phone.
There will also be an Duvix/Quelbran app developed.

Reason: Good things, take time :-)

Reason: I am still waiting for some design to be submitted

```html
<!DOCTYPE html>
<html lang="en">
<head>
<meta charset="utf-8">
<title>Nearpost – Share your thoughts</title>
<link href="https://fonts.googleapis.com/css2?family=Arimo:wght@400;700&display=swap" rel="stylesheet">
<style>
:root{
  --grid-line:#e6e9ed;
  --page:#ffffff;
  --ink:#444444;
  --ink-soft:#333333;
  --brand:#5a5a5a;
  --link:#3d8ac6;
  --accent:#1aa0e0;
  --banner:#c5dbf1;
  --banner-line:#b7cfe8;
  --bar-top:#e3f0fa;
  --bar-bottom:#c9e0f3;
  --bar-text:#4a90c8;
  --panel:#dde9f5;
  --panel-border:#bed3e9;
  --rule:#d8d8d8;
  --crown:#f7bd2a;
  --crown-dark:#e59d12;
  --trophy:#1b7fc4;
  --note:#f8e65a;
  --footer:#2b2b2b;
  --footer-text:#d0d0d0;
  --footer-muted:#7a7a7a;
}
*{box-sizing:border-box;margin:0;padding:0}
html,body{width:1179px;height:1200px;overflow:hidden}
body{
  font-family:"Arimo",Arial,sans-serif;color:var(--ink);
  background-color:#fbfbfb;
  background-image:linear-gradient(var(--grid-line) 1px,transparent 1px),linear-gradient(90deg,var(--grid-line) 1px,transparent 1px);
  background-size:10px 10px;
}
.stage{position:relative;width:1152px;height:1173px;transform:scale(1.0234);transform-origin:0 0}
.abs{position:absolute}
.brand-name{left:122px;top:24px;font-size:32px;font-weight:700;color:var(--brand)}
.search-field{left:730px;top:30px;width:242px;height:29px;background:#8a8a8a;border-radius:3px;color:#f2f2f2;font-size:14px;padding:6px 12px}
.search-button{left:979px;top:30px;width:72px;height:28px;border-radius:3px;background:linear-gradient(#eef6fc,#cfe4f5);color:var(--bar-text);font-size:14px;font-weight:700;text-align:center;line-height:28px}
.page{left:95px;top:82px;width:961px;height:996px;background:var(--page)}
.banner{left:95px;top:82px;width:961px;height:164px;background-color:var(--banner);
  background-image:linear-gradient(var(--banner-line) 1px,transparent 1px),linear-gradient(90deg,var(--banner-line) 1px,transparent 1px);background-size:10px 10px;border-radius:3px 3px 0 0}
.banner h1{position:absolute;left:37px;top:40px;font-size:35px;line-height:43px;font-weight:700;letter-spacing:2.4px;color:#5b5b5b}
.bubble{position:absolute;background:#a9c3dc;border-radius:50%}
.bar{left:95px;top:246px;width:961px;height:71px;background:linear-gradient(var(--bar-top),var(--bar-bottom))}
.bar-title{left:138px;top:268px;font-size:23px;color:var(--bar-text)}
.field{height:24px;background:linear-gradient(#fff,#eef5fb);border-radius:2px;color:var(--bar-text);font-size:15px;font-weight:700;padding:3px 8px;display:flex;justify-content:space-between}
.yes{left:928px;top:258px;font-size:36px;font-weight:700;color:#5a9bd0;letter-spacing:-1px}
.feed-title{left:134px;top:322px;font-size:13px;color:var(--link)}
.feed{left:134px;top:340px;width:532px;border-top:1px solid var(--rule)}
.post{display:flex;align-items:center;border-bottom:1px solid var(--rule);position:relative}
.avatar{width:62px;height:48px;background:linear-gradient(#6c6c6c,#2f2f2f);border:1px solid #999;flex:none}
.post-body{margin-left:20px;width:360px}
.post-name{font-size:15px;color:var(--ink);margin-bottom:6px}
.post-name span{color:var(--accent)}
.post-text{font-size:12px;letter-spacing:.3px;line-height:14px;color:var(--ink-soft)}
.post-icon{position:absolute;left:496px;top:50%;transform:translateY(-50%);width:56px;height:52px}
.side{left:745px;top:337px;width:257px;height:328px;background:var(--panel);border:1px solid var(--panel-border);border-radius:4px}
.side-title{position:absolute;left:8px;top:7px;font-size:13px;color:var(--link)}
.side-item{position:absolute;left:17px;width:219px;height:55px;border-bottom:3px solid #cad9e7;display:flex;align-items:center}
.side-item svg{width:56px;height:48px;flex:none}
.side-item p{margin-left:18px;font-size:12px;line-height:17px;color:var(--ink-soft);letter-spacing:.2px}
.side-item p span{color:var(--link);display:block}
.follow{position:absolute;left:27px;top:288px;font-size:23px;color:#5a9bd0}
.social{position:absolute;top:292px;width:22px;height:22px;border-radius:3px;background:#4f86c6}
.handsets{left:753px;top:681px;font-size:12px;color:#222}
.store-badge{left:748px;top:710px;width:253px;height:83px;border-radius:8px;background:linear-gradient(#8a8a8a,#5d5d5d);border:2px solid #b8b8b8}
.mini{border-radius:4px}
.phone{top:922px;width:50px;height:100px;border-radius:8px}
.footer{left:92px;top:1078px;width:965px;height:95px;background:var(--footer)}
.footer-line{left:118px;font-size:12px;color:var(--footer-text)}
.footer-line a{color:var(--footer-text);text-decoration:none;margin-right:14px}
.footer-more{left:898px;top:1118px;font-size:13px;color:var(--footer-muted)}
</style>
</head>
<body>
<svg width="0" height="0" style="position:absolute">
  <defs>
    <symbol id="crown" viewBox="0 0 56 52">
      <path d="M8 20 L18 30 L28 12 L38 30 L48 20 L44 44 L12 44 Z" fill="var(--crown)" stroke="var(--crown-dark)" stroke-width="2" stroke-linejoin="round"/>
      <circle cx="8" cy="18" r="5" fill="var(--crown)" stroke="var(--crown-dark)" stroke-width="2"/>
      <circle cx="28" cy="10" r="5" fill="var(--crown)" stroke="var(--crown-dark)" stroke-width="2"/>
      <circle cx="48" cy="18" r="5" fill="var(--crown)" stroke="var(--crown-dark)" stroke-width="2"/>
    </symbol>
    <symbol id="trophy" viewBox="0 0 56 52">
      <circle cx="28" cy="26" r="24" fill="var(--trophy)" stroke="#0f5f9a" stroke-width="2"/>
      <circle cx="28" cy="26" r="19" fill="#2d95d8"/>
      <path d="M19 14 H37 V22 C37 28 33 31 28 31 C23 31 19 28 19 22 Z M26 31 H30 V36 H34 V40 H22 V36 H26 Z" fill="#0e3f66"/>
    </symbol>
    <symbol id="note" viewBox="0 0 56 52">
      <path d="M6 2 H52 V40 L42 50 H6 Z" fill="var(--note)" stroke="#e0c93a" stroke-width="2"/>
      <path d="M14 16 H44 M14 24 H44 M14 32 H44" stroke="#d8be2a" stroke-width="2"/>
    </symbol>
  </defs>
</svg>

<div class="stage">
  <div class="abs brand-name">Nearpost</div>
  <div class="abs search-field">search...</div>
  <div class="abs search-button">Search</div>

  <div class="abs page"></div>

  <section class="abs banner">
    <div class="bubble" role="img" aria-label="speech bubble decoration" style="left:471px;top:24px;width:38px;height:30px;opacity:.7"></div>
    <div class="bubble" role="img" aria-label="speech bubble decoration" style="left:497px;top:80px;width:60px;height:48px;opacity:.7"></div>
    <h1>Share your thoughts<br>in your neighbourhood!</h1>
  </section>

  <div class="abs bar"></div>
  <div class="abs bar-title">sign up &amp; Join</div>
  <div class="abs field" style="left:345px;top:270px;width:185px">Address:</div>
  <div class="abs field" style="left:576px;top:270px;width:129px">Radius&nbsp; 1.km <span>⬍</span></div>
  <div class="abs field" style="left:752px;top:270px;width:130px">Radius <span>⬍</span></div>
  <div class="abs yes">yes!</div>

  <div class="abs feed-title">Whats going on now</div>
  <div class="abs feed">
    <div class="post" style="height:76px"><div class="avatar" role="img" aria-label="member portrait"></div><div class="post-body"><p class="post-name">Dana Pruitt - <span>CEO</span></p><p class="post-text">Duis Aliquet Egestas Purus In Blandit. Curabitur Vulputate,</p></div><svg class="post-icon"><use href="#crown"/></svg></div>
    <div class="post" style="height:80px"><div class="avatar" role="img" aria-label="member portrait"></div><div class="post-body"><p class="post-name">Dana Pruitt - <span>CEO</span></p><p class="post-text">Duis Aliquet Egestas Purus In Blandit. Curabitur Vulputate,<br>Ligula Lacinia Scelerisque Tempor, Lacus</p></div><svg class="post-icon"><use href="#crown"/></svg></div>
    <div class="post" style="height:80px"><div class="avatar" role="img" aria-label="member portrait"></div><div class="post-body"><p class="post-name">Dana Pruitt - <span>CEO</span></p><p class="post-text">Duis Aliquet Egestas Purus In Blandit. Curabitur Vulputate,</p></div><svg class="post-icon"><use href="#crown"/></svg></div>
    <div class="post" style="height:78px"><div class="avatar" role="img" aria-label="member portrait"></div><div class="post-body"><p class="post-name">Dana Pruitt - <span>CEO</span></p><p class="post-text">Duis Aliquet Egestas Purus In Blandit. Curabitur Vulputate,</p></div><svg class="post-icon"><use href="#trophy"/></svg></div>
    <div class="post" style="height:76px"><div class="avatar" role="img" aria-label="member portrait"></div><div class="post-body"><p class="post-name">Dana Pruitt - <span>CEO</span></p><p class="post-text">Duis Aliquet Egestas Purus In Blandit. Curabitur Vulputate,<br>Ligula Lacinia Scelerisque Tempor, Lacus</p></div><svg class="post-icon"><use href="#note"/></svg></div>
    <div class="post" style="height:78px"><div class="avatar" role="img" aria-label="member portrait"></div><div class="post-body"><p class="post-name">Dana Pruitt - <span>CEO</span></p><p class="post-text">Duis Aliquet Egestas Purus In Blandit. Curabitur Vulputate,</p></div><svg class="post-icon"><use href="#crown"/></svg></div>
    <div class="post" style="height:78px"><div class="avatar" role="img" aria-label="member portrait"></div><div class="post-body"><p class="post-name">Dana Pruitt - <span>CEO</span></p><p class="post-text">Duis Aliquet Egestas Purus In Blandit. Curabitur Vulputate,</p></div><svg class="post-icon"><use href="#trophy"/></svg></div>
    <div class="post" style="height:76px"><div class="avatar" role="img" aria-label="member portrait"></div><div class="post-body"><p class="post-name">Dana Pruitt - <span>CEO</span></p><p class="post-text">Duis Aliquet Egestas Purus In Blandit. Curabitur Vulputate,<br>Ligula Lacinia Scelerisque Tempor, Lacus</p></div><svg class="post-icon"><use href="#note"/></svg></div>
    <div class="post" style="height:78px;border-bottom:none"><div class="avatar" role="img" aria-label="member portrait"></div><div class="post-body"><p class="post-name">Dana Pruitt - <span>CEO</span></p><p class="post-text">Duis Aliquet Egestas Purus In Blandit. Curabitur Vulputate,</p></div><svg class="post-icon"><use href="#crown"/></svg></div>
  </div>

  <aside class="abs side">
    <p class="side-title">Whats going on now</p>
    <div class="side-item" style="top:24px"><svg><use href="#crown"/></svg><p><span>Duis Aliquet Egestas</span>Duis Aliquet Egestas</p></div>
    <div class="side-item" style="top:80px"><svg><use href="#crown"/></svg><p><span>Duis Aliquet Egestas</span>Duis Aliquet Egestas</p></div>
    <div class="side-item" style="top:140px"><svg><use href="#crown"/></svg><p><span>Duis Aliquet Egestas</span>Duis Aliquet Egestas</p></div>
    <div class="side-item" style="top:200px"><svg><use href="#crown"/></svg><p><span>Duis Aliquet Egestas</span>Duis Aliquet Egestas</p></div>
    <p class="follow">Follow us</p>
    <span class="social" style="left:149px"></span>
    <span class="social" style="left:184px;background:#5cb8e4"></span>
    <span class="social" style="left:220px;background:#2f7bb5"></span>
  </aside>

  <p class="abs handsets">this is available acroos all available handsets.</p>
  <div class="abs store-badge" role="img" aria-label="app store badge"></div>
  <div class="abs mini" role="img" aria-label="handset store badge" style="left:748px;top:805px;width:80px;height:28px;background:#d6d6d6"></div>
  <div class="abs mini" role="img" aria-label="handset store badge" style="left:872px;top:806px;width:130px;height:24px;background:#e3efc6"></div>
  <div class="abs mini" role="img" aria-label="handset store badge" style="left:748px;top:848px;width:78px;height:48px;background:linear-gradient(90deg,#6c5aa8,#d24a8c)"></div>
  <div class="abs mini" role="img" aria-label="handset store badge" style="left:853px;top:846px;width:52px;height:50px;background:#e8e8e8"></div>
  <div class="abs mini" role="img" aria-label="handset store badge" style="left:948px;top:850px;width:49px;height:48px;border-radius:10px;background:linear-gradient(#6fb7ef,#1d6fc6)"></div>
  <div class="abs phone" role="img" aria-label="red handset photo" style="left:747px;background:linear-gradient(#c0202a,#6a0f15)"></div>
  <div class="abs phone" role="img" aria-label="silver handset photo" style="left:818px;background:linear-gradient(#d9dde2,#7b8794)"></div>
  <div class="abs phone" role="img" aria-label="black touchscreen handset photo" style="left:889px;background:linear-gradient(#6a7380,#1d2126)"></div>
  <div class="abs phone" role="img" aria-label="black keyboard handset photo" style="left:954px;background:linear-gradient(#4a4a4a,#141414)"></div>

  <footer class="abs footer"></footer>
  <p class="abs footer-line" style="top:1096px">© larkwave&nbsp; 2011&nbsp; e. support@larkwave.com.au</p>
  <p class="abs footer-line" style="top:1116px"><a href="#">terms &amp; conditions</a><a href="#">privacy policy</a><a href="#">customer service</a><a href="#">register</a><a href="#">sitemap</a></p>
  <p class="abs footer-more">further information</p>
</div>
</body>
</html>
```